Glimmerquo Frozen Yogurt

I am looking for a postcard to use for advertising purposes. We are a self serve frozen business that serves frozen yogurt, ice cream and gelato. We also have smoothies, milkshakes, waffle cones and waffle bowls. We have a bottoms bar and extensive toppings bar with only premium toppings and syrups.

Our main colors are purple, lime green and orange and the store is very
bright but not focused on kids, it is more trendy.

We have over 40 different candy, fruit and syrup toppings to choose from.
We give back to our community in many ways, as well as holding fundraising
for our local schools, churches and charities.
Updates

Project Deadline Extended Reason: I haven't found anything that I really like. Added Friday, March 10, 2017

Target Market(s)

young and mature alike

Industry/Entity Type

Business

Font styles to use
Sans Serif

Colors
6b449b
add136
f37122

Requirements
Must have
• color, our colors are lime green, purple and orange.
Nice to have
• I would like to have some type of discount on there. Maybe a 20% off their purchase with the postcard.

```html
<!DOCTYPE html>
<html lang="en">
<head>
<meta charset="utf-8">
<title>Glimmerquo Frozen Yogurt – Postcard</title>
<link href="https://fonts.googleapis.com/css2?family=Roboto+Slab:wght@700&family=Open+Sans:wght@400;700&family=Cabin+Sketch:wght@700&family=Courgette&family=Roboto+Condensed:wght@700&display=swap" rel="stylesheet">
<style>
  :root{
    --backdrop:#5c3815;
    --purple:#6b449b;
    --purple-deep:#7a2f93;
    --lime:#add136;
    --green:#5cb63a;
    --orange:#f37122;
    --red:#e8212a;
    --yellow:#ffe000;
    --ink:#333333;
    --panel:#e6e7e8;
    --social:#3b5998;
    --white:#ffffff;
  }
  *{margin:0;padding:0;box-sizing:border-box}
  html,body{width:826px;height:1200px;overflow:hidden;background:var(--backdrop)}
  .canvas{position:relative;width:826px;height:1200px}
  .card{position:absolute;left:61px;width:699px;height:541px;background:var(--white);overflow:hidden;box-shadow:4px 5px 8px rgba(0,0,0,.45)}
  .card--front{top:38px;
    background:
      radial-gradient(circle at 75% 20%, rgba(255,200,220,.3) 0 60px, transparent 62px),
      radial-gradient(circle at 60% 35%, rgba(255,240,170,.3) 0 50px, transparent 52px),
      radial-gradient(circle at 88% 12%, rgba(200,230,255,.3) 0 45px, transparent 47px),
      radial-gradient(circle at 70% 82%, rgba(230,210,255,.25) 0 60px, transparent 62px),
      var(--white);}
  .card--back{top:610px}

  .brand{position:absolute;font-family:"Open Sans",sans-serif}
  .brand__name{display:block;color:var(--lime);font-weight:700;line-height:1}
  .brand__tag{display:block;color:var(--purple);font-weight:700;letter-spacing:.02em}
  .card--front .brand{left:34px;top:50px}
  .card--front .brand__name{font-size:46px}
  .card--front .brand__tag{font-size:17px;margin-top:8px}
  .brand__dot{position:absolute;border-radius:50%;background:var(--orange)}
  .card--front .brand__dot{left:270px;top:-22px;width:30px;height:30px}

  .headline{position:absolute;right:30px;top:32px;text-align:right;font-family:"Roboto Slab",serif;font-weight:700;line-height:.9;text-transform:uppercase;letter-spacing:-1px}
  .headline__small{display:block;font-size:33px;color:var(--purple-deep)}
  .headline__big{display:block;font-size:44px;color:var(--green)}

  .swoosh{position:absolute;left:0;top:0}
  .cup-photo{position:absolute;left:28px;top:150px;width:250px;height:320px;border-radius:38% 38% 30% 30%;
    background:linear-gradient(180deg,#fbfbfb 0%,#d63a3a 38%,#f0efe8 62%,#e6e3da 100%)}

  .offer{position:absolute;right:30px;top:206px;text-align:right;font-family:"Roboto Slab",serif;font-weight:700;font-size:32px;line-height:1.05;color:var(--white);letter-spacing:-.5px}
  .slogan{position:absolute;left:420px;top:296px;font-family:"Cabin Sketch",sans-serif;font-weight:700;font-size:46px;line-height:1.1;color:var(--white)}
  .discount{position:absolute;left:285px;top:318px;width:110px;text-align:center;font-family:"Roboto Condensed",sans-serif;font-weight:700;font-size:38px;line-height:.9;color:#4a3a12}

  .phone{position:absolute;font-family:"Roboto Condensed",sans-serif;font-weight:700}
  .card--front .phone{right:30px;top:430px;font-size:36px;color:var(--ink)}
  .tagline{position:absolute;left:269px;top:494px;font-family:"Courgette",cursive;font-size:16px;color:var(--purple-deep)}
  .social-button{position:absolute;left:527px;top:483px;width:136px;height:44px;border-radius:4px;background:var(--social);color:var(--white);font-family:"Open Sans",sans-serif;font-weight:700;display:flex;align-items:center;gap:8px;padding-left:8px}
  .social-button__square{width:26px;height:26px;background:#5f7fc0;border-radius:2px;flex:none}
  .social-button__text{font-size:12px;line-height:1.1}
  .social-button__text b{font-size:17px;display:block}

  .dessert-photo{position:absolute;left:0;top:0;width:330px;height:290px;border-bottom-right-radius:60px;
    background:linear-gradient(135deg,#f6dbe6 0%,#f3b9cf 35%,#f7d67a 65%,#f3e6d4 100%)}
  .splash{position:absolute;left:300px;top:0;width:180px;height:400px;
    background:linear-gradient(200deg,rgba(225,225,225,.8) 0%,rgba(255,255,255,0) 75%)}
  .social-circle{position:absolute;left:27px;top:25px;width:48px;height:48px;border-radius:50%;background:#7a6a5c;border:3px solid #d9d2c8}
  .card--back .brand{left:343px;top:74px}
  .card--back .brand__name{font-size:26px}
  .card--back .brand__tag{font-size:10px;margin-top:4px}
  .card--back .brand__dot{left:152px;top:-18px;width:22px;height:22px}

  .contact{position:absolute;left:0;width:340px;top:310px;text-align:center;color:var(--ink)}
  .contact__address{font-family:"Open Sans",sans-serif;font-size:15px;line-height:1.5;font-style:normal}
  .card--back .phone{position:static;display:block;margin-top:10px;font-size:30px;color:var(--purple-deep);line-height:1}
  .contact__web{display:block;font-family:"Roboto Slab",serif;font-weight:700;font-size:22px;letter-spacing:.08em;color:var(--purple-deep);margin-top:2px}

  .mail-panel{position:absolute;background:var(--panel);font-family:"Open Sans",sans-serif;font-size:15px;color:#222;display:flex;align-items:center;justify-content:center}
  .mail-panel--stamp{left:530px;top:14px;width:160px;height:162px;align-items:flex-start;padding-top:62px}
  .mail-panel--address{left:339px;top:174px;width:351px;height:356px;align-items:flex-start;padding-top:154px}
  .mail-panel--barcode{left:0;top:450px;width:339px;height:80px}
</style>
</head>
<body>
<main class="canvas">

  <section class="card card--front" aria-label="Postcard front">
    <svg class="swoosh" width="699" height="541" viewBox="0 0 699 541" aria-hidden="true">
      <path d="M0 215 C120 190 300 210 410 260 L410 440 C300 520 140 540 0 530 Z" fill="var(--lime)"/>
      <path d="M0 225 C120 202 290 220 395 268 L395 430 C290 505 140 522 0 518 Z" fill="var(--red)"/>
      <path d="M436 286 C440 240 520 190 699 186 L699 286 Z" fill="var(--yellow)"/>
      <path d="M442 286 C450 246 525 198 699 194 L699 286 Z" fill="var(--red)"/>
      <rect x="388" y="282" width="311" height="140" fill="var(--lime)"/>
      <rect x="388" y="287" width="311" height="129" fill="var(--purple-deep)"/>
      <ellipse cx="340" cy="354" rx="70" ry="54" fill="var(--yellow)" stroke="var(--orange)" stroke-width="3"/>
    </svg>

    <div class="cup-photo" role="img" aria-label="Photo of a frozen yogurt cup topped with whipped cream, berries and cookie pieces"></div>

    <div class="brand">
      <span class="brand__dot" aria-hidden="true"></span>
      <span class="brand__name">Glimmerquo</span>
      <span class="brand__tag">FROZEN YOGURT</span>
    </div>

    <h1 class="headline">
      <span class="headline__small">Our Yogurt</span>
      <span class="headline__big">Creamier</span>
      <span class="headline__small">&amp; More</span>
      <span class="headline__big">Delicious</span>
    </h1>

    <p class="offer">Buy One<br>Get One Free</p>
    <p class="discount">20%<br>OFF</p>
    <p class="slogan">GRAB A CUP,<br>LOAD IT UP!</p>

    <p class="phone">302-555-0148</p>
    <p class="tagline">Fresh fruit, best flavours &amp; toppings</p>
    <div class="social-button">
      <span class="social-button__square" aria-hidden="true"></span>
      <span class="social-button__text">Like Us<b>Online</b></span>
    </div>
  </section>

  <section class="card card--back" aria-label="Postcard back">
    <div class="splash" role="img" aria-label="Soft milk splash"></div>
    <div class="dessert-photo" role="img" aria-label="Photo of ice cream scoops with strawberries, mint and wafer sticks in a glass bowl"></div>
    <span class="social-circle" aria-hidden="true"></span>

    <div class="brand">
      <span class="brand__dot" aria-hidden="true"></span>
      <span class="brand__name">Glimmerquo</span>
      <span class="brand__tag">FROZEN YOGURT</span>
    </div>

    <div class="contact">
      <address class="contact__address">1187 Marlowe Rd<br>Fenwick Grove Shopping Center<br>Brindle Falls, DE 19890</address>
      <span class="phone">302-555-0148</span>
      <span class="contact__web">www.glimmerquo.com</span>
    </div>

    <div class="mail-panel mail-panel--stamp">stamp</div>
    <div class="mail-panel mail-panel--address">Address area</div>
    <div class="mail-panel mail-panel--barcode">Barcode area</div>
  </section>

</main>
</body>
</html>
```